Black Matte card with samurai logo which I would like it to be textured and company name on one side and on the other side I would like the company information with the reno (Face logo) Sushi logo. Double Sided card.

majority customers are University students, University sororities and fraternities.

It Company

Reno Sushi
317 W. Harlow Ave
Tucson, AZ 85042
Phone (520)413-6271
Fax (520)357-1846
E-mail: Renosushidesert@mailbox-example.com
FB: Renosushidesert
Twitter: Renosushidesert

• Present Normal

```html
<!DOCTYPE html>
<html lang="en">
<head>
<meta charset="utf-8">
<title>Reno Sushi – Business Card</title>
<link rel="stylesheet" href="https://fonts.googleapis.com/css2?family=Open+Sans:wght@400;600&display=swap">
<style>
  :root {
    --page: #ece7e1;
    --card-black: #151515;
    --card-charcoal: #2c2c2c;
    --brand-red: #b3322a;
    --ink: #3a3a3a;
    --paper: #ffffff;
    --rule: #cfcfcf;
  }
  * { box-sizing: border-box; margin: 0; padding: 0; }
  html, body { width: 1177px; height: 1200px; overflow: hidden; }
  body {
    background: var(--page);
    font-family: "Open Sans", Arial, sans-serif;
    position: relative;
  }
  .card {
    position: absolute;
    width: 955px;
    height: 540px;
    border-radius: 42px;
    overflow: hidden;
  }
  /* Front side */
  .card--front {
    left: 24px; top: 43px;
    background:
      repeating-linear-gradient(180deg, rgba(255,255,255,0.04) 0 2px, rgba(0,0,0,0) 2px 9px),
      radial-gradient(ellipse at 50% 40%, var(--card-charcoal), var(--card-black) 75%);
  }
  .front-mark {
    position: absolute;
    left: 50%; top: 150px;
    transform: translateX(-50%);
    width: 64px; height: 64px;
    border-radius: 50%;
    background: var(--brand-red);
  }
  .front-name {
    position: absolute;
    left: 0; right: 0; top: 380px;
    text-align: center;
    color: var(--brand-red);
    font-size: 92px;
    font-weight: 400;
    line-height: 1;
    letter-spacing: 1px;
  }
  /* Back side */
  .card--back {
    left: 196px; top: 623px;
    background: var(--paper);
    border: 2px solid #222;
  }
  .back-brand {
    position: absolute;
    left: 60px; top: 120px;
    width: 320px;
    text-align: center;
  }
  .back-brand__mark {
    display: block;
    width: 46px; height: 46px;
    margin: 0 auto 28px;
    border-radius: 50%;
    background: var(--brand-red);
  }
  .back-brand__name {
    color: var(--brand-red);
    font-size: 52px;
    font-weight: 400;
    line-height: 1;
  }
  .back-divider {
    position: absolute;
    left: 420px; top: 115px;
    width: 1px; height: 225px;
    background: var(--rule);
  }
  .contact {
    position: absolute;
    left: 445px; top: 120px;
    list-style: none;
    color: var(--ink);
    font-size: 22px;
    line-height: 40px;
  }
  .contact li { display: flex; align-items: center; gap: 10px; white-space: nowrap; }
  .contact svg { width: 22px; height: 22px; flex: none; }
  .address {
    position: absolute;
    left: 477px; top: 248px;
    color: var(--ink);
    font-size: 22px;
    line-height: 32px;
    font-style: normal;
  }
  .swoosh { position: absolute; left: 0; bottom: 0; width: 955px; height: 150px; }
  .social {
    position: absolute;
    left: 650px; top: 440px;
    list-style: none;
    color: var(--paper);
    font-size: 22px;
    line-height: 38px;
  }
  .social li { display: flex; align-items: center; gap: 10px; }
  .social__square { width: 22px; height: 22px; background: var(--brand-red); flex: none; }
</style>
</head>
<body>

  <section class="card card--front" aria-label="Card front">
    <span class="front-mark" aria-hidden="true"></span>
    <h1 class="front-name">Reno Sushi</h1>
  </section>

  <section class="card card--back" aria-label="Card back">
    <div class="back-brand">
      <span class="back-brand__mark" aria-hidden="true"></span>
      <p class="back-brand__name">Reno Sushi</p>
    </div>

    <div class="back-divider"></div>

    <ul class="contact">
      <li>
        <svg viewBox="0 0 24 24" aria-hidden="true"><circle cx="12" cy="12" r="11" fill="none" stroke="#b3322a" stroke-width="2"/><path d="M8 6c-1 1-1 3 1 6s4 5 6 5c1 0 2-1 2-2l-2-2-2 1c-1-1-2-2-3-4l1-2-2-2z" fill="#b3322a"/></svg>
        (520)413-6271
      </li>
      <li>
        <svg viewBox="0 0 24 24" aria-hidden="true"><rect x="6" y="3" width="12" height="7" fill="#b3322a"/><rect x="2" y="10" width="20" height="9" rx="2" fill="#b3322a"/><rect x="6" y="14" width="12" height="2" fill="#fff"/></svg>
        (520)357-1846
      </li>
      <li>
        <svg viewBox="0 0 24 24" aria-hidden="true"><rect x="2" y="6" width="20" height="13" rx="2" fill="#b3322a"/><path d="M3 7l9 7 9-7" fill="none" stroke="#fff" stroke-width="2"/></svg>
        Renosushidesert@mailbox-example.com
      </li>
    </ul>

    <address class="address">
      317 W. Harlow Ave Tucson<br>
      AZ 85042
    </address>

    <svg class="swoosh" viewBox="0 0 955 150" preserveAspectRatio="none" aria-hidden="true">
      <path d="M0 150 L0 60 C260 20 560 -5 955 25 L955 150 Z" fill="#222"/>
      <path d="M0 45 C260 5 560 -15 955 12" fill="none" stroke="#222" stroke-width="4"/>
      <path d="M0 150 L0 95 C260 70 500 55 720 55 C470 75 260 110 170 150 Z" fill="#b3322a"/>
    </svg>

    <ul class="social">
      <li><span class="social__square" aria-hidden="true"></span>Renosushidesert</li>
      <li><span class="social__square" aria-hidden="true"></span>Renosushidesert</li>
    </ul>
  </section>

</body>
</html>
```